BrivoTerna. Lantern of the Steady Harvest. Business card

Professional business card for BrivoTerna (Lantern of the Steady Harvest)
My rationale: Strategy-> Execution-> Results-> Value that lead to the BrivoTerna name: We put the Lantern of the Steady Harvest.
We deliver value to our customers helping them at defining a good strategy (cyan arrow). 90% of well formulated strategies fail due to poor execution so we also consider strategical execution very important (green arrow). Due to the execution we obtain the results (blue arrow). Finally, the results provide feedback to redefine strategy, and the new strategy has to be executed and new results obtained providing new feedback and on and on. It's like a wheel that finally, must create corporate value: value for shareholders, staholders, employees, providers...-

Target Market(s)

CEOs and steering comitees , invewrnent funds

Industry/Entity Type

Business Consultant

Contact Information for Business Card

Teodoro Vinsquel
CEO & Founder
teodoro.vinsquel@brivoterna-example.com
Mobile: +34 655.803.912
www.brivoterna-example.com

Colors

Designer to choose colors to be used in the design.

Requirements
Nice to have
• Nice to hace the words: Strategy, execution, results
• Nice to vave the claim: Lantern of the Steady Harvest
• The three colors should be shown:
• cyan for STRATEGY
• green for EXECUTION
• blue for RESULTS
Should not have
• Complete black background

```html
<!DOCTYPE html>
<html lang="en">
<head>
<meta charset="utf-8">
<title>BrivoTerna — Business Card</title>
<link rel="stylesheet" href="https://fonts.googleapis.com/css2?family=Source+Sans+3:wght@400;600;700&display=swap">
<style>
  :root {
    --page-bg: #e6e7ea;
    --card-bg: #f3f4f6;
    --card-edge: #dcdee3;
    --brand-blue: #0a3a9e;
    --name-blue: #1b3f9c;
    --text-grey: #4a4d52;
    --icon-blue: #1f4aa8;
    --results-blue: #8a9fcf;
    --execution-green: #b7d69a;
    --strategy-cyan: #7cc4e2;
  }
  * { box-sizing: border-box; margin: 0; padding: 0; }
  html, body {
    width: 1200px;
    height: 1077px;
    overflow: hidden;
    background: var(--page-bg);
    font-family: "Source Sans 3", "Myriad Pro", sans-serif;
  }
  .business-card {
    position: absolute;
    left: 100px;
    top: 253px;
    width: 1000px;
    height: 571px;
    background: var(--card-bg);
    border: 1px solid var(--card-edge);
    border-radius: 30px;
    box-shadow: 0 14px 40px rgba(40, 50, 70, 0.12);
  }
  .brand-name {
    position: absolute;
    left: 40px;
    top: 58px;
    font-size: 84px;
    font-weight: 700;
    letter-spacing: -2px;
    line-height: 1;
    color: var(--brand-blue);
  }
  .brand-mark-area {
    position: absolute;
    left: 540px;
    top: 88px;
    width: 400px;
    height: 392px;
    border-radius: 24px;
    background: linear-gradient(160deg,
      var(--results-blue) 0%,
      var(--execution-green) 55%,
      var(--strategy-cyan) 100%);
    opacity: 0.55;
  }
  .person {
    position: absolute;
    left: 44px;
    top: 300px;
  }
  .person-name {
    font-size: 33px;
    font-weight: 700;
    color: var(--name-blue);
    line-height: 1.1;
  }
  .person-role {
    margin-top: 6px;
    font-size: 26px;
    font-weight: 400;
    color: var(--text-grey);
  }
  .contact-list {
    position: absolute;
    left: 44px;
    top: 424px;
    list-style: none;
  }
  .contact-item {
    display: flex;
    align-items: center;
    gap: 14px;
    height: 40px;
    font-size: 25px;
    color: var(--text-grey);
  }
  .contact-icon {
    width: 22px;
    height: 22px;
    flex: none;
  }
</style>
</head>
<body>
  <main class="business-card">
    <div class="brand-name">BrivoTerna</div>

    <div class="brand-mark-area" role="img" aria-label="Brand mark area in the strategy cyan, execution green and results blue tones"></div>

    <section class="person">
      <h1 class="person-name">Teodoro Vinsquel</h1>
      <p class="person-role">CEO &amp; Founder</p>
    </section>

    <ul class="contact-list">
      <li class="contact-item">
        <svg class="contact-icon" viewBox="0 0 22 22" aria-hidden="true">
          <rect x="5" y="1.5" width="12" height="19" rx="2.5" fill="none" stroke="var(--icon-blue)" stroke-width="2"/>
          <circle cx="11" cy="16.5" r="1.4" fill="var(--icon-blue)"/>
        </svg>
        <span>+34 655.803.912</span>
      </li>
      <li class="contact-item">
        <svg class="contact-icon" viewBox="0 0 22 22" aria-hidden="true">
          <rect x="1.5" y="5" width="19" height="13" rx="1.5" fill="none" stroke="var(--icon-blue)" stroke-width="2"/>
          <path d="M2 6 L11 13 L20 6" fill="none" stroke="var(--icon-blue)" stroke-width="2"/>
        </svg>
        <span>teodoro.vinsquel@brivoterna-example.com</span>
      </li>
      <li class="contact-item">
        <svg class="contact-icon" viewBox="0 0 22 22" aria-hidden="true">
          <circle cx="11" cy="11" r="8.5" fill="none" stroke="var(--icon-blue)" stroke-width="1.8"/>
          <ellipse cx="11" cy="11" rx="3.8" ry="8.5" fill="none" stroke="var(--icon-blue)" stroke-width="1.5"/>
          <path d="M2.5 11 H19.5 M4 6.5 H18 M4 15.5 H18" stroke="var(--icon-blue)" stroke-width="1.4"/>
        </svg>
        <span>www.brivoterna-example.com</span>
      </li>
    </ul>
  </main>
</body>
</html>
```